Push notification screens at app start up

We have an existing news publication app platform and are adding categories to push notifications.

We need two screens designed (each for Zorbel, Quillet and Android for a total of 6d) that show when the app is first launched.

The workflow of our app:
0. app launch screen while webservices run (no work needed)
1. information screen to the user promoting the benefits of push notification with "Next" button. (see concept attached)
2. Push categories selection screen. This will have list of category types, with on/off switch.

"Select the categories that you wish to receive occasional notices:
Breaking News (on/off switch)
Local News (on/off switch)
Sports (on/off switch)
Local Events (on/off switch)
Weather Alerts (on/off switch)
Local Deals (on/off switch)"

"Enable these categories on the next screen."
"Next" button

Background:
When I was looking around at app designs, I came across this one (http://www.plinthworks.example/design/7719034) and I really liked it. We obviously have different features on our screen, but I’d like to have this same feel. The colors used in this design are perfect.

UPDATE: I do not mean to limit your design to match the layout as the one mentioned above. Please use your creativity for the layout.

Our standard font in Helvetica Neue.

Notes:
- our app is developed for all phone devices from Zorbel 4 to Zorbel 6, so designs should be thoughtful of vertical scrolling if needed.
- our app is developed for Quillets, so we'll need designs completed as well. (We can finalize Zorbel design first, then translate the design to Quillet.)
- our app is developed for Android phones (not tablets), so we'll need designs completed as well. (We can finalize iOS design first, then translater to Android UI design guidelines).

We hope to establish a good on-going relationship with the designer for as-needed work in the future.

News

• Helvetica Neue

• Clean designs. No clutter.
• We would likely go with the standard on/off switches for both iOS and Android, but are open to small custom variations.

```html
<!DOCTYPE html>
<html lang="en">
<head>
<meta charset="utf-8">
<title>Push Notice Categories</title>
<link rel="stylesheet" href="https://fonts.googleapis.com/css2?family=Arimo:wght@400;700&display=swap">
<style>
  :root {
    --brand-blue: #3a9ae0;
    --brand-blue-deep: #2f8fd8;
    --white: #ffffff;
    --label-grey: #58595b;
    --icon-grey: #8a8c8e;
    --divider: #dcdcdc;
    --switch-off-border: #e3e3e3;
    --page-bg: #ffffff;
  }
  * { box-sizing: border-box; margin: 0; padding: 0; }
  html, body {
    width: 675px;
    height: 1200px;
    overflow: hidden;
    background: var(--page-bg);
    font-family: "Arimo", "Helvetica Neue", Helvetica, Arial, sans-serif;
  }
  .screen {
    position: relative;
    width: 675px;
    height: 1200px;
    background: var(--page-bg);
    overflow: hidden;
  }
  .app-header {
    position: absolute;
    left: 0; top: 0;
    width: 675px;
    height: 153px;
    background: var(--brand-blue);
    color: var(--white);
  }
  .status-bar {
    position: absolute;
    left: 0; top: 0;
    width: 100%;
    height: 34px;
    font-size: 16px;
    font-weight: 700;
    color: var(--white);
  }
  .status-left {
    position: absolute;
    left: 12px; top: 8px;
    display: flex;
    align-items: center;
    gap: 8px;
  }
  .status-time {
    position: absolute;
    left: 0; right: 0; top: 8px;
    text-align: center;
  }
  .status-right {
    position: absolute;
    right: 12px; top: 7px;
    display: flex;
    align-items: center;
    gap: 8px;
  }
  .header-message {
    position: absolute;
    left: 0; right: 0; top: 42px;
    text-align: center;
    font-size: 25px;
    font-weight: 700;
    line-height: 35px;
  }
  .intro {
    position: absolute;
    left: 0; right: 0; top: 186px;
    text-align: center;
    font-size: 25px;
    line-height: 34px;
    color: var(--brand-blue);
  }
  .category-list {
    position: absolute;
    left: 0; top: 299px;
    width: 675px;
    list-style: none;
    border-top: 2px solid var(--divider);
  }
  .category {
    position: relative;
    height: 99px;
    border-bottom: 2px solid var(--divider);
  }
  .category-icon {
    position: absolute;
    left: 28px; top: 33px;
  }
  .category-name {
    position: absolute;
    left: 100px; top: 33px;
    font-size: 28px;
    font-weight: 700;
    color: var(--label-grey);
  }
  .switch {
    position: absolute;
    left: 568px; top: 23px;
    width: 90px;
    height: 52px;
    border-radius: 26px;
    border: 3px solid var(--switch-off-border);
    background: var(--white);
  }
  .switch::after {
    content: "";
    position: absolute;
    left: 1px; top: 1px;
    width: 44px; height: 44px;
    border-radius: 50%;
    background: var(--white);
    box-shadow: 0 2px 5px rgba(0,0,0,0.28);
  }
  .switch.is-on {
    background: var(--brand-blue);
    border-color: var(--brand-blue);
  }
  .switch.is-on::after { left: 39px; }
  .next-button {
    position: absolute;
    left: 27px; top: 1069px;
    width: 621px;
    height: 97px;
    background: var(--brand-blue-deep);
    color: var(--white);
    border: none;
    border-radius: 4px;
    font-family: inherit;
    font-size: 40px;
    font-weight: 700;
    text-align: center;
    line-height: 97px;
  }
</style>
</head>
<body>
<main class="screen">
  <header class="app-header">
    <div class="status-bar">
      <div class="status-left">
        <svg width="52" height="10" viewBox="0 0 52 10" aria-hidden="true">
          <circle cx="5" cy="5" r="4.5" fill="#fff"/>
          <circle cx="15" cy="5" r="4.5" fill="#fff"/>
          <circle cx="25" cy="5" r="4.5" fill="#fff"/>
          <circle cx="35" cy="5" r="4" fill="none" stroke="#fff" stroke-width="1"/>
          <circle cx="45" cy="5" r="4" fill="none" stroke="#fff" stroke-width="1"/>
        </svg>
        <span class="carrier">NOVA</span>
        <svg width="20" height="15" viewBox="0 0 20 15" aria-hidden="true">
          <path d="M10 14 L1 5 A13 13 0 0 1 19 5 Z" fill="#fff"/>
        </svg>
      </div>
      <div class="status-time">4:21 PM</div>
      <div class="status-right">
        <svg width="10" height="17" viewBox="0 0 10 17" aria-hidden="true">
          <path d="M1 4.5 L8.5 12 L5 15.5 V1.5 L8.5 5 L1 12.5" fill="none" stroke="#fff" stroke-width="1.5"/>
        </svg>
        <span>100%</span>
        <svg width="42" height="18" viewBox="0 0 42 18" aria-hidden="true">
          <rect x="1" y="1" width="36" height="16" rx="3" fill="none" stroke="#fff" stroke-width="1.5"/>
          <rect x="3.5" y="3.5" width="31" height="11" rx="1.5" fill="#fff"/>
          <rect x="38.5" y="6" width="2.5" height="6" rx="1" fill="#fff"/>
        </svg>
      </div>
    </div>
    <p class="header-message">You must enable Push Notices on<br>the next screen to apply these settings.</p>
  </header>

  <p class="intro">Select the categories of notices you<br>wish to receive:</p>

  <ul class="category-list">
    <li class="category">
      <svg class="category-icon" width="32" height="30" viewBox="0 0 32 30" aria-hidden="true">
        <rect x="1" y="1" width="30" height="28" fill="none" stroke="var(--icon-grey)" stroke-width="2"/>
        <rect x="6" y="6" width="8" height="8" fill="var(--icon-grey)"/>
        <path d="M17 7h9M17 12h9M6 18h20M6 23h20" stroke="var(--icon-grey)" stroke-width="2"/>
      </svg>
      <span class="category-name">Breaking News</span>
      <span class="switch" role="switch" aria-checked="false"></span>
    </li>
    <li class="category">
      <svg class="category-icon" width="32" height="30" viewBox="0 0 32 30" aria-hidden="true">
        <rect x="1" y="1" width="30" height="28" fill="none" stroke="var(--icon-grey)" stroke-width="2"/>
        <rect x="6" y="6" width="8" height="8" fill="var(--icon-grey)"/>
        <path d="M17 7h9M17 12h9M6 18h20M6 23h20" stroke="var(--icon-grey)" stroke-width="2"/>
      </svg>
      <span class="category-name">Local News</span>
      <span class="switch is-on" role="switch" aria-checked="true"></span>
    </li>
    <li class="category">
      <svg class="category-icon" width="32" height="30" viewBox="0 0 32 30" aria-hidden="true">
        <rect x="1" y="1" width="30" height="28" fill="none" stroke="var(--icon-grey)" stroke-width="2"/>
        <rect x="6" y="6" width="8" height="8" fill="var(--icon-grey)"/>
        <path d="M17 7h9M17 12h9M6 18h20M6 23h20" stroke="var(--icon-grey)" stroke-width="2"/>
      </svg>
      <span class="category-name">Sports</span>
      <span class="switch" role="switch" aria-checked="false"></span>
    </li>
    <li class="category">
      <svg class="category-icon" width="32" height="30" viewBox="0 0 32 30" aria-hidden="true">
        <rect x="1" y="1" width="30" height="28" fill="none" stroke="var(--icon-grey)" stroke-width="2"/>
        <rect x="6" y="6" width="8" height="8" fill="var(--icon-grey)"/>
        <path d="M17 7h9M17 12h9M6 18h20M6 23h20" stroke="var(--icon-grey)" stroke-width="2"/>
      </svg>
      <span class="category-name">Local Events</span>
      <span class="switch" role="switch" aria-checked="false"></span>
    </li>
    <li class="category">
      <svg class="category-icon" width="32" height="30" viewBox="0 0 32 30" aria-hidden="true">
        <rect x="1" y="1" width="30" height="28" fill="none" stroke="var(--icon-grey)" stroke-width="2"/>
        <rect x="6" y="6" width="8" height="8" fill="var(--icon-grey)"/>
        <path d="M17 7h9M17 12h9M6 18h20M6 23h20" stroke="var(--icon-grey)" stroke-width="2"/>
      </svg>
      <span class="category-name">Weather Alerts</span>
      <span class="switch" role="switch" aria-checked="false"></span>
    </li>
    <li class="category">
      <svg class="category-icon" width="32" height="30" viewBox="0 0 32 30" aria-hidden="true">
        <rect x="1" y="1" width="30" height="28" fill="none" stroke="var(--icon-grey)" stroke-width="2"/>
        <rect x="6" y="6" width="8" height="8" fill="var(--icon-grey)"/>
        <path d="M17 7h9M17 12h9M6 18h20M6 23h20" stroke="var(--icon-grey)" stroke-width="2"/>
      </svg>
      <span class="category-name">Local Deals</span>
      <span class="switch" role="switch" aria-checked="false"></span>
    </li>
  </ul>

  <button class="next-button" type="button">NEXT</button>
</main>
</body>
</html>
```